Calloway Hotel

A Hotel (Pub) in Sydney CBD. Posters will be outside of Hotel informing People what is on in Hotel.
We will be Printing in A1 size.
CALLOWAY HOTEL
Open 9am - 3am 7 Days
Monday - Thursday
Happy Hour
4pm - 6pm
Local Beer & Wine
Wednesday
Poker Night: Great $$$ Prizes
Everyday
Steak or Schniztels: Served with Mashed Potato & Salad or Chips & Salad - $8.50
Live Sport on the Big Screen
BISTRO
OPEN 7 DAYS 12- 9pm
Daily Blackboard Specials + Full Menu Inside
Best service in Town
Target Market(s)
Male or Female 18 to Seniors.Passing Trade.
Industry/Entity Type
Hotel
Look and feel
Each slider illustrates characteristics of the customer's brand and the style your logo design should communicate.

```html
<!DOCTYPE html>
<html lang="en">
<head>
<meta charset="utf-8">
<title>Calloway Hotel – What's On</title>
<link rel="stylesheet" href="https://fonts.googleapis.com/css2?family=Alfa+Slab+One&family=Oswald:wght@600&display=swap">
<style>
  :root {
    --night-deep: #15153d;
    --night-mid: #2c2c72;
    --night-glow: #5454a8;
    --skyline-top: #4a4a92;
    --skyline-bottom: #23233f;
    --water: #3c3d58;
    --signal-red: #e3242b;
    --white: #ffffff;
    --ink: #111122;
  }
  * { margin: 0; padding: 0; box-sizing: border-box; }
  html, body { width: 848px; height: 1200px; overflow: hidden; background: var(--night-deep); }
  .poster {
    position: relative;
    width: 848px;
    height: 1200px;
    overflow: hidden;
    background: radial-gradient(ellipse at 50% 45%, var(--night-glow) 0%, var(--night-mid) 45%, var(--night-deep) 100%);
  }
  .city-scene {
    position: absolute;
    left: 0; top: 520px;
    width: 848px; height: 680px;
    background: linear-gradient(180deg, rgba(74,74,146,0) 0%, var(--skyline-top) 28%, var(--skyline-bottom) 65%, var(--water) 100%);
  }
  .line {
    position: absolute;
    left: 0; width: 100%;
    text-align: center;
    white-space: nowrap;
    line-height: 1;
  }
  .hotel-name {
    font-family: "Alfa Slab One", serif;
    color: var(--white);
    font-size: 80px;
    letter-spacing: 12px;
  }
  .hours {
    font-family: "Alfa Slab One", serif;
    font-variant: small-caps;
    color: var(--white);
    font-size: 28px;
    letter-spacing: 2px;
    text-shadow: 2px 2px 0 var(--ink);
  }
  .headline, .offer {
    font-family: "Alfa Slab One", serif;
    font-variant: small-caps;
    color: var(--signal-red);
    text-shadow: 2px 0 0 var(--white), -2px 0 0 var(--white), 0 2px 0 var(--white), 0 -2px 0 var(--white), 3px 3px 0 var(--ink);
  }
  .headline { font-size: 50px; letter-spacing: 3px; }
  .offer { font-size: 36px; letter-spacing: 3px; }
  .bistro-title {
    font-family: "Alfa Slab One", serif;
    color: var(--white);
    font-size: 40px;
    letter-spacing: 3px;
    text-shadow: 3px 3px 0 var(--ink);
  }
  .bistro-info {
    font-family: "Alfa Slab One", serif;
    font-variant: small-caps;
    color: var(--white);
    font-size: 28px;
    letter-spacing: 2px;
    text-shadow: 2px 0 0 var(--ink), -2px 0 0 var(--ink), 0 2px 0 var(--ink), 0 -2px 0 var(--ink);
  }
  .bistro-info.small { font-size: 24px; letter-spacing: 1px; }
  .happy-hour {
    font-family: "Oswald", sans-serif;
    font-weight: 600;
    font-variant: small-caps;
    color: var(--signal-red);
    font-size: 38px;
    letter-spacing: -0.5px;
    text-shadow: 2px 2px 0 var(--ink);
  }
</style>
</head>
<body>
<main class="poster">
  <div class="city-scene" role="img" aria-label="Night photograph of the Sydney city skyline across the harbour water"></div>

  <h1 class="line hotel-name" style="top:16px;">CALLOWAY</h1>
  <div class="line hotel-name" style="top:110px;">HOTEL</div>

  <p class="line hours" style="top:230px;">Open 9am - 3am ,7 Days</p>

  <h2 class="line headline" style="top:279px;">Wednesday</h2>
  <p class="line offer" style="top:362px;">Poker Night: Great $$$ Prizes</p>

  <h2 class="line headline" style="top:405px;">Everyday</h2>
  <p class="line offer" style="top:506px;">Steak or Schniztels: Served with</p>
  <p class="line offer" style="top:578px;">Mashed Potato &amp; Salad or Chips &amp;</p>
  <p class="line offer" style="top:654px;">Salad - $8.50</p>

  <p class="line headline" style="top:735px;">Live Sport on the Big</p>
  <p class="line headline" style="top:786px;">Screen</p>

  <h2 class="line bistro-title" style="top:904px;">BISTRO</h2>
  <p class="line bistro-info" style="top:994px;">Open 7 Days 12- 9pm</p>
  <p class="line bistro-info small" style="top:1032px;">Daily Blackboard Specials+ Full Menu Inside</p>
  <p class="line bistro-info small" style="top:1066px;">Best Service in Town</p>

  <p class="line happy-hour" style="top:1137px;">Monday - Thursday,Happy Hour-4pm - 6pm,Local Beer &amp; Wine</p>
</main>
</body>
</html>
```